Coastline Premier Retreats Business Card Design

Design a business card for Coastline Premier Retreats. Look at the website for colors and reference. Card should have logo, name, title, office number, mobile number, email, URL and a tagline like, "Luxury Hotel & Resort Email Marketing" (This might change).

https://www.coastlinepremierretreats.example

The rest I will leave up to your imagination.

Contact Information for Business Card

Logo, name, title, office number, mobile number, email, URL and a tagline like, "Luxury Hotel & Resort Email Marketing" (This might change).

```html
<!DOCTYPE html>
<html lang="en">
<head>
<meta charset="utf-8">
<title>Coastline Premier Retreats – Business Card</title>
<link rel="stylesheet" href="https://fonts.googleapis.com/css2?family=Open+Sans:wght@400;600;700;800&display=swap">
<style>
  :root {
    --backdrop: #c4c4c4;
    --card: #fdfdf6;
    --ink: #111111;
    --accent: #f07622;
    --edge: rgba(0,0,0,0.18);
  }
  * { margin: 0; padding: 0; box-sizing: border-box; }
  html, body {
    width: 1200px; height: 780px; overflow: hidden;
    background: var(--backdrop);
    font-family: "Open Sans", Arial, sans-serif;
    color: var(--ink);
  }
  .stage {
    width: 1200px; height: 780px;
    display: flex; align-items: center; justify-content: center; gap: 40px;
  }
  .card {
    position: relative;
    width: 560px; height: 320px;
    background: var(--card);
    box-shadow: 0 6px 18px var(--edge);
    overflow: hidden;
  }

  /* Front side */
  .card-front {
    display: flex; align-items: center; justify-content: center;
  }
  .brand-large {
    display: flex; align-items: center; gap: 14px;
  }
  .brand-large .brand-square {
    width: 22px; height: 22px; background: var(--accent);
  }
  .brand-large .brand-name {
    font-weight: 800; font-size: 30px; letter-spacing: 0.5px;
    color: var(--ink); line-height: 1.05; text-transform: uppercase;
  }

  /* Back side */
  .brand-small {
    position: absolute; left: 36px; top: 38px;
    display: flex; align-items: center; gap: 9px;
  }
  .brand-small .brand-square {
    width: 12px; height: 12px; background: var(--accent);
  }
  .brand-small .brand-name {
    font-weight: 800; font-size: 15px; letter-spacing: 0.3px;
    text-transform: uppercase; line-height: 1.1;
  }

  .person {
    position: absolute; right: 44px; top: 66px; text-align: right;
  }
  .person-name {
    font-weight: 700; font-size: 26px; line-height: 1.1;
  }
  .person-name .first { color: var(--accent); }
  .person-name .last { color: var(--ink); }
  .person-title {
    font-weight: 600; font-size: 13px; margin-top: 2px;
  }
  .accent-bar {
    position: absolute; right: 0; top: 62px;
    width: 22px; height: 54px; background: var(--accent);
  }

  .tagline {
    position: absolute; left: 40px; top: 160px;
    color: var(--accent); font-size: 14px; line-height: 1.35; font-weight: 400;
  }

  .contacts {
    position: absolute; left: 40px; top: 222px;
    list-style: none; font-size: 13.5px; line-height: 20px;
  }
  .contacts li { display: flex; align-items: center; gap: 10px; }
  .contacts svg { width: 13px; height: 13px; flex: none; fill: var(--accent); }
</style>
</head>
<body>
<main class="stage">

  <section class="card card-front" aria-label="Business card front">
    <div class="brand-large">
      <span class="brand-square"></span>
      <span class="brand-name">Coastline<br>Premier Retreats</span>
    </div>
  </section>

  <section class="card card-back" aria-label="Business card back">
    <div class="brand-small">
      <span class="brand-square"></span>
      <span class="brand-name">Coastline Premier Retreats</span>
    </div>

    <div class="person">
      <p class="person-name"><span class="first">Marina</span> <span class="last">Delacroix</span></p>
      <p class="person-title">Co-Founder</p>
    </div>
    <span class="accent-bar"></span>

    <p class="tagline">Luxury Hotel &amp;<br>Resort Email Marketing</p>

    <ul class="contacts">
      <li>
        <svg viewBox="0 0 16 16" aria-hidden="true"><path d="M3.5 1.5l2.5 0 1 3.5-1.6 1.2c.8 1.8 2.2 3.2 4 4l1.2-1.6 3.5 1v2.5c0 .8-.7 1.5-1.5 1.5C6.8 13.6 2.4 9.2 2 3c0-.8.7-1.5 1.5-1.5z"/></svg>
        (555) 014-2758
      </li>
      <li>
        <svg viewBox="0 0 16 16" aria-hidden="true"><path d="M4.5 1h7a1 1 0 0 1 1 1v12a1 1 0 0 1-1 1h-7a1 1 0 0 1-1-1V2a1 1 0 0 1 1-1zm.5 1.5v10h6v-10z"/></svg>
        (555) 019-7777
      </li>
      <li>
        <svg viewBox="0 0 16 16" aria-hidden="true"><circle cx="8" cy="8" r="7"/><path d="M1 8h14M8 1c2.2 2 2.2 12 0 14M8 1c-2.2 2-2.2 12 0 14" stroke="#fdfdf6" stroke-width="1" fill="none"/></svg>
        www.coastlinepremierretreats.example
      </li>
      <li>
        <svg viewBox="0 0 16 16" aria-hidden="true"><path d="M1 4h14v9H1z"/><path d="M1 4l7 5 7-5" stroke="#fdfdf6" stroke-width="1.2" fill="none"/></svg>
        info@coastlinepremierretreats.example
      </li>
    </ul>
  </section>

</main>
</body>
</html>
```